Detail Shop Business card design

i need a business card design for my new detailing company called 'Brisk's Polish Works'. i want an all black and white design . simple, direct and to the point. i want the designer to choose a fitting font to match the logothe front should have logo, address, phone and email and the back side should have a slogan and text indicating that we offer services on anything including cars, trucks, motorcycles and RVs. slogan will read "we take pride in your ride"
maybe also very small on the back side the IG icon with Brisks_Polish_Works

phone 208.417.6352
address 3847 E Larkin Ave
Spokane WA 99214
email: BrisksPolish@mailvexo.com

Target Market(s)

all ages , auto enthusiasts

Industry/Entity Type

Automotive

Contact Information for Business Card

the front should have logo, address, phone and email and the back side should have a slogan and text indicating that we offer services on anything including cars, trucks, motorcycles and RVs. slogan will read "we take pride in your ride"

phone 208.417.6352
address 3847 E Larkin Ave
Spokane WA 99214

Colors
000000
ffffff

Requirements
Must have
• bold font and very simple design with good spacing
Nice to have
• anything creative from the designer indicating we service any types of vehicles
Should not have
• any colors ,

```html
<!DOCTYPE html>
<html lang="en">
<head>
<meta charset="utf-8">
<title>Brisk's Polish Works – Business Card</title>
<link href="https://fonts.googleapis.com/css2?family=Roboto:wght@400;500;700&family=Oswald:wght@400&display=swap" rel="stylesheet">
<style>
  :root {
    --ink: #000000;
    --paper: #ffffff;
    --backdrop: #e6e6e6;
    --art-light: #e4e4e4;
    --art-mid: #a8a8a8;
    --divider: #bdbdbd;
  }
  html, body {
    margin: 0;
    padding: 0;
    width: 1200px;
    height: 960px;
    overflow: hidden;
    background: var(--backdrop);
    font-family: "Roboto", Arial, sans-serif;
  }
  .canvas { position: relative; width: 1200px; height: 960px; }
  .card {
    position: absolute;
    width: 600px;
    height: 343px;
    background: var(--paper);
    overflow: hidden;
    box-shadow: 0 2px 6px rgba(0,0,0,0.25);
  }
  .card--front { left: 314px; top: 113px; }
  .card--back  { left: 311px; top: 472px; }

  .hero-art {
    position: absolute;
    left: 32px; top: 8px;
    width: 552px; height: 150px;
    border-radius: 12px;
    background: linear-gradient(180deg, var(--art-light) 0%, var(--art-mid) 100%);
  }
  .front-band { position: absolute; left: 0; top: 0; width: 600px; height: 343px; }

  .owner {
    position: absolute;
    right: 339px; top: 230px;
    text-align: right;
    color: var(--paper);
  }
  .owner__name { font-size: 19px; font-weight: 500; letter-spacing: 0.2px; margin: 0; line-height: 24px; }
  .owner__title { font-size: 15px; margin: 0 0 8px; line-height: 20px; }
  .owner__address { font-size: 14px; line-height: 19px; margin: 0; font-style: normal; }

  .front-divider {
    position: absolute;
    left: 282px; top: 230px;
    width: 1px; height: 86px;
    background: var(--divider);
  }
  .contact {
    position: absolute;
    left: 302px; top: 234px;
    margin: 0; padding: 0;
    list-style: none;
    color: var(--paper);
    font-size: 14px;
  }
  .contact li { display: flex; align-items: center; height: 19px; }
  .contact svg { width: 12px; height: 12px; margin-right: 10px; fill: var(--paper); }

  .brand {
    position: absolute;
    left: 0; top: 112px;
    width: 600px;
    text-align: center;
    font-weight: 700;
    font-size: 56px;
    line-height: 70px;
    letter-spacing: 3px;
    color: var(--ink);
  }
  .brand__dot {
    display: inline-block;
    width: 22px; height: 22px;
    border-radius: 50%;
    background: var(--ink);
    margin-left: 14px;
    vertical-align: middle;
  }
  .slogan {
    position: absolute;
    left: 0; top: 270px;
    width: 600px;
    text-align: center;
    font-weight: 700;
    font-size: 17px;
    letter-spacing: 0.3px;
    color: var(--ink);
    margin: 0;
  }
  .slogan-rule {
    position: absolute;
    left: 137px; top: 293px;
    width: 325px; height: 2px;
    background: var(--ink);
  }
  .services {
    position: absolute;
    left: 0; top: 297px;
    width: 600px;
    text-align: center;
    font-family: "Oswald", "Arial Narrow", sans-serif;
    font-size: 12.5px;
    color: var(--ink);
    margin: 0;
  }
</style>
</head>
<body>
<div class="canvas">

  <section class="card card--front">
    <div class="hero-art" role="img" aria-label="Black and white illustration of a vintage hot rod with exposed engine"></div>
    <svg class="front-band" viewBox="0 0 600 343" aria-hidden="true">
      <path d="M0 210 Q 300 160 600 212 L600 343 L0 343 Z" fill="var(--ink)"/>
    </svg>

    <div class="owner">
      <p class="owner__name">DALE MERCER</p>
      <p class="owner__title">CEO/FOUNDER</p>
      <address class="owner__address">3847 E Larkin Ave<br>Spokane WA 99214</address>
    </div>

    <div class="front-divider"></div>

    <ul class="contact">
      <li><svg viewBox="0 0 12 12"><path d="M2.5 0.5 L4.5 0.5 L5.2 3.2 L3.8 4.4 Q5 7 7.6 8.2 L8.8 6.8 L11.5 7.5 L11.5 9.5 Q11.5 11.5 9.5 11.5 Q0.5 10.5 0.5 2.5 Q0.5 0.5 2.5 0.5 Z"/></svg>208.417.6352</li>
      <li><svg viewBox="0 0 12 12"><path d="M3 0 H9 Q10 0 10 1 V11 Q10 12 9 12 H3 Q2 12 2 11 V1 Q2 0 3 0 Z M3.2 1.5 V9.5 H8.8 V1.5 Z M5.2 10.2 H6.8 V11.2 H5.2 Z"/></svg>208 731 5820</li>
      <li><svg viewBox="0 0 12 12"><path d="M0.5 2.5 H11.5 V9.5 H0.5 Z M1.2 3 L6 6.6 L10.8 3 Z" fill-rule="evenodd"/></svg>BrisksPolish@mailvexo.com</li>
      <li><svg viewBox="0 0 12 12"><circle cx="6" cy="6" r="5.5"/><path d="M3 3.5 Q5 3 5.5 5 Q4 6.5 3 5.5 Z M7 7 Q9 6.5 9.5 8.5 Q8 10 7 9 Z" fill="var(--ink)"/></svg>www.briskspolish.com</li>
    </ul>
  </section>

  <section class="card card--back">
    <div class="brand">BRISK'S<span class="brand__dot"></span></div>
    <p class="slogan">WE TAKE PRIDE IN YOUR RIDE</p>
    <div class="slogan-rule"></div>
    <p class="services">we offer services on anything including cars, trucks, motorcycles &amp; RVS</p>
  </section>

</div>
</body>
</html>
```